Business Card

Just need business logo with phone number on it. 0487 312 654
And the following on the bottom of the card.

"Your local plumbing experts".
and emblems for zelpa card, cheque and cash

```html
<!DOCTYPE html>
<html lang="en">
<head>
<meta charset="utf-8">
<title>Ridgeway Plumbing &amp; Drainage – Business Card</title>
<link rel="stylesheet" href="https://fonts.googleapis.com/css2?family=Saira:wght@400;700&display=swap">
<style>
  :root {
    --backdrop: #1e1e1e;
    --card-white: #ffffff;
    --brand-red: #ec1c24;
    --brand-blue: #1a96d4;
    --ink: #1a1a1a;
    --radius: 10px;
  }
  html, body {
    margin: 0;
    padding: 0;
    width: 1200px;
    height: 900px;
    overflow: hidden;
    background: var(--backdrop);
    font-family: "Saira", sans-serif;
  }
  .canvas {
    position: relative;
    width: 1200px;
    height: 900px;
  }
  .card {
    position: absolute;
    top: 306px;
    width: 439px;
    height: 271px;
    border-radius: var(--radius);
    overflow: hidden;
  }
  .card--front {
    left: 149px;
    background: var(--card-white);
  }
  .card--back {
    left: 608px;
    background: linear-gradient(to top right,
      var(--brand-red) 3%,
      var(--brand-blue) 42%,
      var(--brand-blue) 58%,
      var(--brand-red) 97%);
  }

  .phone {
    position: absolute;
    top: 34px;
    right: 22px;
    display: flex;
    align-items: center;
    gap: 4px;
    font-size: 16px;
    color: var(--ink);
    letter-spacing: 0.2px;
  }
  .phone__icon { width: 21px; height: 21px; }

  .brand-name {
    position: absolute;
    margin: 0;
    font-weight: 700;
    text-transform: uppercase;
    line-height: 1;
  }
  .card--front .brand-name {
    left: 22px;
    top: 96px;
    color: var(--brand-red);
    font-size: 27px;
    letter-spacing: 1.5px;
  }
  .brand-name__sub {
    display: block;
    font-size: 13.4px;
    letter-spacing: 2.6px;
    margin-top: 5px;
  }
  .card--back .brand-name {
    left: 0;
    right: 0;
    top: 104px;
    text-align: center;
    color: var(--card-white);
    font-size: 34px;
    letter-spacing: 2px;
  }
  .card--back .brand-name__sub {
    font-size: 16.2px;
    letter-spacing: 3.4px;
    margin-top: 6px;
  }

  .divider {
    position: absolute;
    left: 26px;
    top: 199px;
    width: 387px;
    height: 2px;
    background: var(--brand-red);
  }

  .tagline {
    position: absolute;
    left: 23px;
    top: 230px;
    margin: 0;
    font-size: 16px;
    color: var(--ink);
    line-height: 1;
  }

  .payments {
    position: absolute;
    left: 240px;
    top: 221px;
    display: flex;
    gap: 9px;
    align-items: center;
  }
  .payment {
    width: 48px;
    height: 30px;
    box-sizing: border-box;
    border-radius: 2px;
    display: flex;
    align-items: center;
    justify-content: center;
  }
  .payment--card {
    border: 1px solid #c9c9c9;
    gap: 3px;
    font-size: 12px;
    font-weight: 700;
    color: var(--brand-blue);
  }
  .payment--card .payment__dot {
    width: 6px;
    height: 6px;
    background: var(--brand-blue);
  }
  .payment--cash { background: #000; }
  .payment--cheque { width: 57px; }
  .payment svg { display: block; }
</style>
</head>
<body>
<main class="canvas">

  <section class="card card--front" aria-label="Business card front">
    <div class="phone">
      <svg class="phone__icon" viewBox="0 0 22 22" aria-hidden="true">
        <circle cx="11" cy="11" r="9.5" fill="none" stroke="var(--brand-red)" stroke-width="1.8"/>
        <path d="M6.5 10.2c0-1.6 2-2.6 4.5-2.6s4.5 1 4.5 2.6l-1.7.3-.4-1.2c-1.5-.5-3.3-.5-4.8 0l-.4 1.2z" fill="var(--brand-blue)"/>
        <path d="M8.3 11h5.4l1.3 3.3H7z" fill="var(--brand-blue)"/>
      </svg>
      <span>0487 312 654</span>
    </div>

    <h1 class="brand-name">Ridgeway<span class="brand-name__sub">Plumbing &amp; Drainage</span></h1>

    <div class="divider"></div>

    <p class="tagline">Your local plumbing experts</p>

    <div class="payments">
      <div class="payment payment--card" aria-label="zelpa card accepted">
        <span class="payment__dot"></span>zelpa
      </div>
      <div class="payment payment--cash" aria-label="Cash accepted">
        <svg width="20" height="20" viewBox="0 0 20 20" aria-hidden="true">
          <circle cx="10" cy="10" r="8.5" fill="#fff"/>
          <text x="10" y="14.2" text-anchor="middle" font-family="Saira, sans-serif" font-weight="700" font-size="12" fill="#000">$</text>
        </svg>
      </div>
      <div class="payment payment--cheque" aria-label="Cheque accepted">
        <svg width="57" height="30" viewBox="0 0 57 30" aria-hidden="true">
          <rect x="3" y="4" width="53" height="24" rx="1" fill="#000"/>
          <rect x="1" y="2" width="53" height="24" rx="1" fill="#fff" stroke="#000" stroke-width="1.4"/>
          <line x1="6" y1="6" x2="14" y2="6" stroke="#000" stroke-width="1"/>
          <rect x="37" y="7" width="13" height="3" fill="none" stroke="#000" stroke-width="1"/>
          <line x1="6" y1="13" x2="49" y2="13" stroke="#000" stroke-width="1"/>
          <line x1="6" y1="17" x2="49" y2="17" stroke="#000" stroke-width="1"/>
          <rect x="6" y="20" width="12" height="3" fill="none" stroke="#000" stroke-width="1"/>
          <line x1="32" y1="22" x2="49" y2="22" stroke="#000" stroke-width="1"/>
        </svg>
      </div>
    </div>
  </section>

  <section class="card card--back" aria-label="Business card back">
    <h2 class="brand-name">Ridgeway<span class="brand-name__sub">Plumbing &amp; Drainage</span></h2>
  </section>

</main>
</body>
</html>
```